Essential Oil 15ml - package of 6

Design of a box of 6 different essential oils.
+ design of the bottle stickers
My bottles are 15ml clear blue glass.

The pictures attached are my competitors...

Target Market(s)

TERVIK USA

Font styles to use
Serif

Requirements
Must have
• Our logo + "essential oil" and type (lavender, eucalyptus etc....)
• 15ml - 0.50 fl.oz.
• special color for the oil type.

```html
<!DOCTYPE html>
<html lang="en">
<head>
<meta charset="utf-8">
<title>Tamar Grove – Essential Oil Box Dieline</title>
<link rel="stylesheet" href="https://fonts.googleapis.com/css2?family=Marcellus&family=Fira+Sans:wght@300;400&display=swap">
<style>
  :root {
    --navy: #10133f;
    --gold-dark: #a85e2c;
    --gold-light: #edb365;
    --page: #ffffff;
    --cut-line: #3a2a1a;
  }
  html, body {
    margin: 0;
    padding: 0;
    width: 1200px;
    height: 1200px;
    overflow: hidden;
    background: var(--page);
  }
  .dieline {
    display: block;
    width: 1200px;
    height: 1200px;
  }
  .panel-front { fill: var(--navy); }
  .fold-line { stroke: var(--cut-line); stroke-width: 1.5; stroke-dasharray: 12 12; fill: none; }
  .brand-mark { fill: var(--gold-light); }
  .brand-name {
    font-family: "Marcellus", serif;
    font-weight: 400;
    font-size: 46px;
    fill: var(--gold-light);
  }
  .lid-name {
    font-family: "Marcellus", serif;
    font-weight: 400;
    font-size: 38px;
    fill: var(--navy);
  }
  .product-line {
    font-family: "Fira Sans", sans-serif;
    font-weight: 400;
    font-size: 28px;
    fill: var(--gold-light);
  }
  .product-size {
    font-family: "Fira Sans", sans-serif;
    font-weight: 300;
    font-size: 18px;
    fill: var(--gold-light);
  }
</style>
</head>
<body>
<svg class="dieline" viewBox="0 -265 1500 1500" xmlns="http://www.w3.org/2000/svg" aria-label="Flat dieline of the Tamar Grove essential oil box">
  <defs>
    <linearGradient id="gold-sheen" x1="0" y1="0" x2="1" y2="1">
      <stop offset="0" stop-color="var(--gold-dark)"/>
      <stop offset="0.5" stop-color="var(--gold-light)"/>
      <stop offset="1" stop-color="var(--gold-dark)"/>
    </linearGradient>
    <linearGradient id="gold-band" x1="0" y1="0" x2="1" y2="0">
      <stop offset="0" stop-color="var(--gold-dark)"/>
      <stop offset="0.55" stop-color="var(--gold-light)"/>
      <stop offset="1" stop-color="var(--gold-dark)"/>
    </linearGradient>
  </defs>

  <!-- glue flap -->
  <polygon class="flap-glue" fill="url(#gold-sheen)" points="15,360 80,340 80,690 15,632"/>

  <!-- top flaps and lid -->
  <polygon class="flap-dust" fill="url(#gold-sheen)" points="530,160 768,160 772,292 782,300 782,340 518,340 518,295 530,290"/>
  <path class="panel-lid" fill="url(#gold-sheen)" d="M782,340 V55 Q782,15 822,15 H1180 Q1220,15 1220,55 V340 Z"/>
  <text class="lid-name" x="1001" y="222" text-anchor="middle">Tamar Grove</text>
  <polygon class="flap-dust" fill="url(#gold-sheen)" points="1235,165 1470,163 1475,290 1484,310 1484,340 1220,340 1220,295 1228,290"/>

  <!-- bottom flaps -->
  <polygon class="flap-bottom" fill="url(#gold-sheen)" points="80,690 515,690 515,918 370,918 350,888 255,888 255,905 220,955 80,955"/>
  <line class="fold-line" x1="475" y1="750" x2="360" y2="870"/>
  <polygon class="flap-bottom" fill="url(#gold-sheen)" points="518,690 782,690 700,865 540,865"/>
  <polygon class="flap-bottom" fill="url(#gold-sheen)" points="782,690 1218,690 1218,918 1073,918 1053,888 958,888 958,905 923,955 782,955"/>
  <line class="fold-line" x1="1178" y1="750" x2="1063" y2="870"/>
  <polygon class="flap-bottom" fill="url(#gold-sheen)" points="1220,690 1484,690 1400,865 1240,865"/>

  <!-- front panel A -->
  <g class="face-front">
    <rect class="panel-front" x="80" y="340" width="438" height="350"/>
    <rect fill="url(#gold-band)" x="80" y="527" width="438" height="48"/>
    <circle class="brand-mark" cx="286" cy="400" r="14"/>
    <text class="brand-name" x="286" y="486" text-anchor="middle">Tamar Grove</text>
    <text class="product-line" x="302" y="647" text-anchor="middle">Pure Essential Oil</text>
    <text class="product-size" x="296" y="678" text-anchor="middle">15 ml/ 6 Bottles</text>
  </g>

  <!-- side panel A -->
  <rect class="panel-side" fill="url(#gold-sheen)" x="518" y="340" width="264" height="350"/>

  <!-- front panel B -->
  <g class="face-back">
    <rect class="panel-front" x="782" y="340" width="438" height="350"/>
    <rect fill="url(#gold-band)" x="782" y="527" width="438" height="48"/>
    <circle class="brand-mark" cx="990" cy="400" r="14"/>
    <text class="brand-name" x="990" y="486" text-anchor="middle">Tamar Grove</text>
    <text class="product-line" x="1008" y="647" text-anchor="middle">Pure Essential Oil</text>
    <text class="product-size" x="1002" y="678" text-anchor="middle">15 ml/ 6 Bottles</text>
  </g>

  <!-- side panel B -->
  <rect class="panel-side" fill="url(#gold-sheen)" x="1220" y="340" width="264" height="350"/>
</svg>
</body>
</html>
```